Income Tax Flyer - Updates Needed

Just need to update this flyer design and give it a new look. We would like to keep all the same wording but make it stand out a little more. Our selling point is the "Same Day Tax Advance up to $6,000"

Lending, Small Loans, Tax Services, Title Loans, Personal Loans

```html
<!DOCTYPE html>
<html lang="en">
<head>
<meta charset="utf-8">
<title>Same Day Tax Advance Flyer</title>
<link href="https://fonts.googleapis.com/css2?family=Poppins:wght@500;600;700;800;900&family=Archivo+Black&family=Anton&family=Cormorant+Garamond:wght@600&display=swap" rel="stylesheet">
<style>
  :root{
    --green:#0f5a2a;
    --green-deep:#0a4720;
    --red:#cc1f2b;
    --red-deep:#a9131d;
    --gold:#dcc000;
    --gold-deep:#b89a00;
    --ink:#1a1a1a;
    --grey:#6d6d6d;
    --grey-dark:#585858;
    --paper:#ffffff;
    --stage:#ededed;
  }
  *{margin:0;padding:0;box-sizing:border-box;}
  html,body{width:1200px;height:3104px;overflow:hidden;background:var(--stage);}
  .flyer{
    position:absolute;left:40px;top:693px;width:1120px;height:1717px;
    background:var(--paper);overflow:hidden;
    font-family:"Poppins",sans-serif;
    box-shadow:0 12px 40px rgba(0,0,0,.25);
  }
  .flyer-bg{position:absolute;inset:0;}
  .photo{position:absolute;}
  .photo-left{left:0;top:200px;width:280px;height:563px;
    background:linear-gradient(160deg,#d9c7b4 0%,#8b8f94 45%,#4c5056 100%);}
  .photo-right{left:900px;top:245px;width:220px;height:518px;
    background:linear-gradient(200deg,#c79a7a 0%,#eeeae6 45%,#cfd6c9 100%);}
  .brand{position:absolute;left:0;right:0;top:120px;text-align:center;color:var(--green);}
  .brand-name{font-family:"Cormorant Garamond",serif;font-weight:600;font-size:80px;line-height:1;}
  .brand-sub{font-family:"Cormorant Garamond",serif;font-weight:600;font-size:22px;letter-spacing:7px;margin-top:4px;}
  .headline{position:absolute;left:0;right:0;text-align:center;line-height:1;}
  .headline-same{top:292px;font-family:"Poppins",sans-serif;font-weight:800;font-size:100px;color:#fff;letter-spacing:1px;}
  .headline-tax{top:395px;font-family:"Archivo Black",sans-serif;font-size:236px;letter-spacing:-6px;
    color:var(--gold);text-shadow:0 4px 0 var(--gold-deep);}
  .headline-adv{top:615px;font-family:"Poppins",sans-serif;font-weight:800;font-size:100px;color:#fff;}
  .price-tag{position:absolute;left:292px;top:750px;width:150px;height:94px;}
  .price-tag span{position:absolute;left:18px;top:26px;font-weight:800;font-size:34px;color:#fff;}
  .price-amount{position:absolute;left:446px;top:722px;font-family:"Anton",sans-serif;font-size:120px;line-height:1;color:#fff;}
  .price-amount sup{font-size:58px;vertical-align:top;position:relative;top:8px;margin-right:4px;}
  .pitch{position:absolute;left:0;right:0;text-align:center;}
  .pitch-line{top:884px;font-weight:700;font-size:45px;color:var(--ink);}
  .pitch-accent{top:934px;font-family:"Archivo Black",sans-serif;font-size:82px;color:var(--green);line-height:1.05;}
  .features{position:absolute;left:72px;top:1346px;width:975px;height:120px;display:flex;gap:4px;}
  .feature{flex:1;display:flex;align-items:center;justify-content:center;text-align:center;
    background:var(--grey);color:#fff;font-weight:600;font-size:31px;line-height:1.2;}
  .feature-mid{background:var(--grey-dark);}
  .contact-title{position:absolute;left:0;right:0;top:1486px;text-align:center;
    font-weight:900;font-size:52px;color:var(--green);letter-spacing:1px;}
  .phone{position:absolute;left:126px;top:1553px;width:476px;height:94px;border-radius:14px;
    background:var(--red);display:flex;align-items:center;padding-left:14px;gap:8px;}
  .phone-number{font-family:"Anton",sans-serif;font-size:66px;color:#fff;line-height:1;}
  .address{position:absolute;left:628px;top:1552px;display:flex;gap:14px;}
  .address-text{font-size:27px;line-height:1.15;color:#333;font-weight:500;}
  .address-text strong{font-weight:700;color:#222;display:block;}
</style>
</head>
<body>
<div class="flyer">
  <svg class="flyer-bg" width="1120" height="1717" viewBox="0 0 1120 1717" aria-hidden="true">
    <defs>
      <radialGradient id="greenGlow" cx="50%" cy="40%" r="70%">
        <stop offset="0" stop-color="#16703a"/><stop offset="1" stop-color="var(--green-deep)"/>
      </radialGradient>
      <radialGradient id="paperGlow" cx="50%" cy="55%" r="60%">
        <stop offset="0" stop-color="#ffffff"/><stop offset="1" stop-color="#ececec"/>
      </radialGradient>
    </defs>
    <rect width="1120" height="1717" fill="url(#paperGlow)"/>
    <path d="M0 0H1120V770L1030 800Q560 760 90 800L0 770Z" fill="url(#greenGlow)"/>
    <path d="M0 725L95 770L0 805Z" fill="var(--red)"/>
    <path d="M1120 725L1025 770L1120 805Z" fill="var(--red)"/>
    <ellipse cx="560" cy="20" rx="320" ry="252" fill="#fff"/>
    <path d="M318 729H800L834 797L800 866H318Z" fill="var(--red)"/>
  </svg>

  <div class="photo photo-left" role="img" aria-label="Photo of a smiling man in a grey suit holding a fan of cash"></div>
  <div class="photo photo-right" role="img" aria-label="Photo of a smiling woman in a white shirt holding cash"></div>

  <div class="brand">
    <div class="brand-name">Northstar</div>
    <div class="brand-sub">LENDING GROUP</div>
  </div>

  <div class="headline headline-same">SAME DAY</div>
  <div class="headline headline-tax">TAX</div>
  <div class="headline headline-adv">ADVANCE</div>

  <div class="price-tag">
    <svg width="150" height="94" viewBox="0 0 150 94" aria-hidden="true">
      <path d="M6 0H112L150 47L112 94H6Q0 94 0 88V6Q0 0 6 0Z" fill="#1e8a3a"/>
    </svg>
    <span>UPTO</span>
  </div>
  <div class="price-amount"><sup>$</sup>6,000</div>

  <div class="pitch pitch-line">FILE YOUR TAXES AND APPLY FOR AN</div>
  <div class="pitch pitch-accent">EASY ADVANCE</div>

  <svg style="position:absolute;left:0;top:1060px" width="1120" height="300" viewBox="0 0 1120 300" aria-hidden="true">
    <g fill="none" stroke-linecap="round">
      <path d="M158 180A120 120 0 0 1 390 100" stroke="var(--ink)" stroke-width="4" stroke-dasharray="2 9"/>
      <circle cx="158" cy="182" r="7" fill="var(--green)" stroke="none"/>
      <path d="M962 180A120 120 0 0 0 730 100" stroke="var(--ink)" stroke-width="4" stroke-dasharray="2 9"/>
      <circle cx="962" cy="182" r="7" fill="var(--green)" stroke="none"/>
      <path d="M446 160A116 116 0 0 0 674 160" stroke="var(--red)" stroke-width="4" stroke-dasharray="2 9"/>
    </g>
    <circle cx="274" cy="135" r="110" fill="#fff" stroke="var(--green)" stroke-width="16"/>
    <circle cx="560" cy="135" r="110" fill="#fff" stroke="var(--red)" stroke-width="16"/>
    <circle cx="852" cy="135" r="110" fill="#fff" stroke="var(--green)" stroke-width="16"/>
    <g fill="#3f3f3f">
      <circle cx="274" cy="135" r="52"/>
      <circle cx="274" cy="135" r="40" fill="#fff"/>
      <rect x="270" y="105" width="8" height="34" rx="3"/>
      <rect x="270" y="131" width="26" height="8" rx="3"/>
      <path d="M274 62A73 73 0 1 1 201 135" fill="none" stroke="#3f3f3f" stroke-width="10"/>
      <path d="M190 138L201 122L214 138Z"/>
      <circle cx="560" cy="105" r="34"/>
      <text x="560" y="120" text-anchor="middle" font-family="Poppins,sans-serif" font-weight="700" font-size="42" fill="#fff">$</text>
      <rect x="500" y="150" width="20" height="44" rx="4"/>
      <path d="M526 154H580Q596 154 596 168H560V174H604L630 158Q642 154 644 166L606 194H526Z"/>
      <path d="M820 120L850 150L850 110Q850 100 860 100Q870 100 870 110V160L900 168Q912 172 908 186L898 212H840L812 182Q806 170 816 166Z"/>
      <rect x="838" y="70" width="6" height="18" rx="3" transform="rotate(-20 841 79)"/>
      <rect x="862" y="66" width="6" height="18" rx="3"/>
      <rect x="884" y="72" width="6" height="18" rx="3" transform="rotate(25 887 81)"/>
    </g>
  </svg>

  <div class="features">
    <div class="feature">Available In<br>24 Hours or Less</div>
    <div class="feature feature-mid">Choose Your<br>Loan Amount</div>
    <div class="feature">Quick<br>and Easy</div>
  </div>

  <div class="contact-title">CONTACT US TODAY!</div>

  <div class="phone">
    <svg width="52" height="52" viewBox="0 0 52 52" aria-hidden="true">
      <circle cx="26" cy="26" r="24" fill="#fff"/>
      <path d="M17 13L23 12L26 20L22 23Q25 30 30 32L33 28L41 31L40 37Q38 41 33 40Q18 36 13 20Q12 15 17 13Z" fill="var(--red)"/>
    </svg>
    <span class="phone-number">2315-480-719</span>
  </div>

  <div class="address">
    <svg width="26" height="30" viewBox="0 0 26 30" aria-hidden="true" style="margin-top:4px">
      <path d="M13 1C6 1 2 6 2 11C2 18 13 27 13 27S24 18 24 11C24 6 20 1 13 1Z" fill="none" stroke="var(--green)" stroke-width="3"/>
      <circle cx="13" cy="11" r="4" fill="var(--green)"/>
    </svg>
    <div class="address-text">
      <strong>Austin – Riverbend</strong>
      4210-2 Meadowlark Ave<br>
      Austin, Texas 78701
    </div>
  </div>
</div>
</body>
</html>
```